Ad for Cyber Security Company- Print Ad

We are looking for an awesome designer to create a one page advertisement for the Kelvora Security data analytics platform that will be featured in an upcoming security magazine. This is also going to be featured in an upcoming trade show. Kelvora Security produced the KELVORA platform to help companies unify their security environment and help them address Insider Threat, Fraud and Anomaly ID and resolution. KELVORA uses an an advanced ingestion engine, machine learning, and workflow automation to ensure the right people are getting the right info at the right time. We serve enterprise level customers, augmenting and enhancing, not replacing their existing security stack. We would like few or single image, clean, and open ad built around the tagline 'Make Security a Team Sport.' We would like the logo to be featured, and include our website address on the page (www.kelvorasecurity.net). See below for style guide.

Target Market(s)

Industry insiders, Chief Information Security Officers (CISO) and Technical directors.

Other font styles liked:
• See style guide, but we are open to suggestion.

Requirements
Must have
• A single image (minimum), Feature the provided logo, Include the tagline 'Make Security a Team Sport' and have the website somewhere on the ad. The image should focus on the conveying the message of "Make Security a Team Sport" and not be a generic security (padlock, network, etc.) image.
• See included style guide.

```html
<!DOCTYPE html>
<html lang="en">
<head>
<meta charset="utf-8">
<title>Kelvora Security – Make Security a Team Sport</title>
<link href="https://fonts.googleapis.com/css2?family=Open+Sans:wght@300;400;600;700;800&display=swap" rel="stylesheet">
<style>
  :root {
    --navy: #0b1150;
    --navy-deep: #080c3a;
    --orange: #ff6622;
    --white: #ffffff;
    --charcoal: #3a3a3c;
    --glow-cyan: #3fd3f0;
    --glow-blue: #2f5ee8;
  }
  * { margin: 0; padding: 0; box-sizing: border-box; }
  html, body { width: 960px; height: 1200px; overflow: hidden; background: var(--navy); }
  .ad {
    position: relative;
    width: 960px;
    height: 1200px;
    font-family: "Open Sans", Arial, sans-serif;
    color: var(--white);
    background: var(--white);
    overflow: hidden;
  }
  .ad__shapes { position: absolute; inset: 0; }
  .brand {
    position: absolute;
    left: 70px;
    top: 62px;
    display: flex;
    align-items: center;
    gap: 16px;
  }
  .brand__square { width: 46px; height: 46px; background: var(--orange); }
  .brand__name {
    font-weight: 800;
    font-size: 40px;
    letter-spacing: 2px;
    line-height: 1;
    color: var(--charcoal);
  }
  .hero-art {
    position: absolute;
    left: 378px;
    top: 200px;
    width: 560px;
    height: 620px;
    background: radial-gradient(ellipse at 50% 42%, rgba(47,94,232,0.75) 0%, rgba(63,211,240,0.35) 35%, rgba(11,17,80,0) 68%);
  }
  .tagline {
    position: absolute;
    left: 96px;
    top: 336px;
    line-height: 1;
    text-transform: uppercase;
  }
  .tagline__line { display: block; font-size: 86px; }
  .tagline__light { font-weight: 300; }
  .tagline__accent { font-weight: 800; color: var(--orange); }
  .tagline__bold { font-weight: 800; }
  .tagline__line--1 { margin-bottom: 14px; }
  .tagline__line--2 { margin-bottom: 20px; }
  .tagline__line--3 { margin-bottom: 12px; }
  .features {
    position: absolute;
    top: 860px;
    left: 0;
    width: 960px;
  }
  .feature {
    position: absolute;
    width: 240px;
    text-align: center;
  }
  .feature--anomaly { left: 100px; }
  .feature--insider { left: 350px; }
  .feature--activity { left: 610px; }
  .feature__icon { display: block; margin: 0 auto; }
  .feature__label {
    margin-top: 28px;
    font-size: 22px;
    font-weight: 400;
    white-space: nowrap;
  }
  .feature__rule {
    width: 32px;
    height: 4px;
    background: var(--orange);
    margin: 14px auto 0;
    border-radius: 2px;
  }
  .social {
    position: absolute;
    left: 0;
    top: 1128px;
    display: flex;
    align-items: center;
    gap: 20px;
  }
  .social__rule { width: 100px; height: 1px; background: var(--orange); }
  .social__dot { width: 42px; height: 42px; border-radius: 50%; background: #2b5cb0; }
  .website {
    position: absolute;
    left: 410px;
    top: 1126px;
    width: 520px;
    text-align: center;
    font-size: 31px;
    letter-spacing: 3px;
    font-weight: 300;
    color: var(--white);
  }
  .website__name { font-weight: 700; }
</style>
</head>
<body>
<main class="ad">
  <svg class="ad__shapes" width="960" height="1200" viewBox="0 0 960 1200" aria-hidden="true">
    <defs>
      <linearGradient id="panelGradient" x1="0" y1="0" x2="1" y2="1">
        <stop offset="0" stop-color="#0d1560"/>
        <stop offset="1" stop-color="#080c3a"/>
      </linearGradient>
    </defs>
    <polygon points="671,28 960,28 960,1200 0,1200 0,170 552,170" fill="url(#panelGradient)"/>
    <polygon points="645,28 674,28 572,150 543,150" fill="var(--orange)"/>
    <polygon points="386,1090 402,1090 340,1200 324,1200" fill="var(--white)"/>
    <polygon points="414,1083 960,1083 960,1200 350,1200" fill="var(--orange)"/>
  </svg>

  <div class="brand">
    <span class="brand__square"></span>
    <span class="brand__name">KELVORA SECURITY</span>
  </div>

  <div class="hero-art" role="img" aria-label="Glowing particle shield with a keyhole at its centre"></div>

  <h1 class="tagline">
    <span class="tagline__line tagline__line--1 tagline__light">Make</span>
    <span class="tagline__line tagline__line--2"><span class="tagline__accent">Security</span> <span class="tagline__light">a</span></span>
    <span class="tagline__line tagline__line--3 tagline__bold">Team</span>
    <span class="tagline__line tagline__bold">Sport</span>
  </h1>

  <section class="features">
    <div class="feature feature--anomaly">
      <svg class="feature__icon" width="92" height="92" viewBox="0 0 92 92" aria-hidden="true">
        <circle cx="46" cy="46" r="44" fill="none" stroke="var(--orange)" stroke-width="2"/>
        <rect x="24" y="26" width="44" height="38" fill="none" stroke="#fff" stroke-width="2"/>
        <line x1="24" y1="32" x2="68" y2="32" stroke="#fff" stroke-width="2"/>
        <line x1="29" y1="40" x2="42" y2="40" stroke="#fff" stroke-width="2"/>
        <line x1="29" y1="46" x2="40" y2="46" stroke="#fff" stroke-width="2"/>
        <line x1="29" y1="52" x2="42" y2="52" stroke="#fff" stroke-width="2"/>
        <circle cx="54" cy="46" r="8" fill="none" stroke="#fff" stroke-width="2"/>
        <line x1="60" y1="52" x2="66" y2="58" stroke="#fff" stroke-width="2"/>
      </svg>
      <p class="feature__label">Anomaly Detection</p>
      <div class="feature__rule"></div>
    </div>
    <div class="feature feature--insider">
      <svg class="feature__icon" width="92" height="92" viewBox="0 0 92 92" aria-hidden="true">
        <circle cx="46" cy="46" r="44" fill="none" stroke="var(--orange)" stroke-width="2"/>
        <rect x="22" y="26" width="48" height="32" fill="none" stroke="#fff" stroke-width="2"/>
        <line x1="46" y1="58" x2="46" y2="66" stroke="#fff" stroke-width="2"/>
        <line x1="36" y1="66" x2="56" y2="66" stroke="#fff" stroke-width="2"/>
        <circle cx="40" cy="40" r="9" fill="none" stroke="#fff" stroke-width="2"/>
        <line x1="47" y1="47" x2="60" y2="60" stroke="#fff" stroke-width="3"/>
      </svg>
      <p class="feature__label">Insider Threat</p>
      <div class="feature__rule"></div>
    </div>
    <div class="feature feature--activity">
      <svg class="feature__icon" width="92" height="92" viewBox="0 0 92 92" aria-hidden="true">
        <circle cx="46" cy="46" r="44" fill="none" stroke="var(--orange)" stroke-width="2"/>
        <rect x="22" y="32" width="44" height="30" fill="none" stroke="#fff" stroke-width="2"/>
        <line x1="44" y1="62" x2="44" y2="68" stroke="#fff" stroke-width="2"/>
        <line x1="36" y1="68" x2="52" y2="68" stroke="#fff" stroke-width="2"/>
        <rect x="32" y="22" width="22" height="26" fill="#0b1150" stroke="#fff" stroke-width="2"/>
        <circle cx="56" cy="50" r="8" fill="#0b1150" stroke="#fff" stroke-width="2"/>
        <line x1="62" y1="56" x2="68" y2="62" stroke="#fff" stroke-width="2"/>
      </svg>
      <p class="feature__label">User Activity Reviews</p>
      <div class="feature__rule"></div>
    </div>
  </section>

  <div class="social">
    <span class="social__rule"></span>
    <span class="social__dot" role="img" aria-label="Social profile link"></span>
    <span class="social__dot" role="img" aria-label="Professional network profile link"></span>
  </div>

  <p class="website">www.<span class="website__name">KelvoraSecurity</span>.net</p>
</main>
</body>
</html>
```